IT Company requires new Business Card design.

Over the years we have had a few different business card designs. We are now due for new cards across the board for all staff. We felt this would be a good time to start fresh with a new design. Our traditional card simply had our details on the front, and a list of services on the back. We don't particularly need the list of services, we have had cards where the only thing on the rear of the card was our logo.
Feel free to be creative, we would like our tag line "Complete IT Management" to appear at some point, doesn't necessarily have to be with the logo.
I have attached samples and drafts of various previous cards we have used over the years.

```html
<!DOCTYPE html>
<html lang="en">
<head>
<meta charset="utf-8">
<title>Pinewood Networking – Business Card</title>
<link rel="stylesheet" href="https://fonts.googleapis.com/css2?family=Open+Sans:wght@400;600;700;800&display=swap">
<style>
  :root {
    --backdrop: #e8e5e2;
    --card: #ffffff;
    --card-edge: #d9d9d9;
    --brand: #5f6c76;
    --text: #3c3c3c;
    --muted: #555b60;
    --rule-light: #e4e4e4;
    --rule-dark: #9a9fa3;
  }
  * { margin: 0; padding: 0; box-sizing: border-box; }
  html, body {
    width: 1034px; height: 1200px; overflow: hidden;
    background: var(--backdrop);
    font-family: "Open Sans", Arial, sans-serif;
  }
  .canvas { position: relative; width: 1034px; height: 1200px; }
  .card {
    position: absolute; left: 75px; width: 897px; height: 510px;
    background: var(--card);
    border: 1px solid var(--card-edge);
    border-radius: 44px;
    box-shadow: 0 3px 10px rgba(0,0,0,0.12);
    overflow: hidden;
  }
  .card--front { top: 69px; }
  .card--back { top: 624px; }

  /* front */
  .brand {
    position: absolute; left: 65px; top: 62px;
    display: flex; align-items: center; gap: 26px;
  }
  .brand__square { width: 118px; height: 118px; background: var(--brand); }
  .brand__name {
    color: var(--brand); font-weight: 800;
    font-size: 66px; line-height: 0.95; letter-spacing: -0.5px;
    text-transform: uppercase;
  }
  .brand__name span { display: block; font-size: 42px; letter-spacing: 1px; }

  .divider {
    position: absolute; left: 0; right: 0; top: 331px; height: 4px;
    background: linear-gradient(to right, var(--rule-light) 0%, var(--rule-light) 40%, var(--rule-dark) 100%);
  }
  .person { position: absolute; right: 65px; top: 286px; text-align: right; }
  .person__name { color: var(--muted); font-size: 27px; font-weight: 700; line-height: 1; }
  .person__role { margin-top: 30px; color: var(--muted); font-size: 21px; }

  .contacts {
    position: absolute; left: 64px; top: 354px;
    list-style: none; color: var(--text); font-size: 21px;
  }
  .contacts li { display: flex; align-items: center; height: 36px; gap: 10px; }
  .contacts svg { width: 20px; height: 20px; fill: var(--text); flex: none; }
  .contacts .pair { margin-left: 12px; display: flex; align-items: center; gap: 8px; }

  .address {
    position: absolute; right: 65px; top: 424px;
    text-align: right; color: var(--text); font-size: 21px; line-height: 36px;
    font-style: normal;
  }

  /* back */
  .back-brand {
    position: absolute; left: 0; right: 0; top: 120px;
    text-align: center; color: var(--brand);
    font-weight: 800; text-transform: uppercase; line-height: 0.9;
  }
  .back-brand__top { font-size: 112px; letter-spacing: -1px; display: block; }
  .back-brand__bottom { font-size: 76px; letter-spacing: 1px; display: block; margin-top: 8px; }
  .tagline {
    position: absolute; left: 0; right: 0; top: 344px;
    text-align: center; color: var(--brand);
    font-size: 26px; font-weight: 400; letter-spacing: 6px; text-transform: uppercase;
  }
  .back-web {
    position: absolute; left: 0; right: 0; top: 452px;
    text-align: center; color: var(--text);
    font-size: 25px; letter-spacing: 2.5px;
  }
  .back-web strong { font-weight: 700; }
</style>
</head>
<body>
<div class="canvas">

  <section class="card card--front" aria-label="Card front">
    <div class="brand">
      <div class="brand__square"></div>
      <div class="brand__name">Pinewood<span>Networking</span></div>
    </div>

    <div class="person">
      <div class="person__name">Daniel Hart</div>
      <div class="person__role">Operation Manager</div>
    </div>
    <div class="divider"></div>

    <ul class="contacts">
      <li>
        <svg viewBox="0 0 20 20" aria-hidden="true"><path d="M10 1a9 9 0 1 0 0 18 9 9 0 0 0 0-18zm0 1.6a7.4 7.4 0 1 1 0 14.8 7.4 7.4 0 0 1 0-14.8zM7 5.2l1.6 2.4-1 1c.6 1.3 1.5 2.2 2.8 2.8l1-1 2.4 1.6-.8 1.8c-3.6-.2-6.6-3.2-6.8-6.8z"/></svg>
        08 9555 0142
        <span class="pair">
          <svg viewBox="0 0 20 20" aria-hidden="true"><path d="M6 1h8a1 1 0 0 1 1 1v16a1 1 0 0 1-1 1H6a1 1 0 0 1-1-1V2a1 1 0 0 1 1-1zm1 2v7h6V3zm0 9v1.5h1.5V12zm2.8 0v1.5h1.5V12zm2.7 0v1.5H14V12zM7 15v1.5h1.5V15zm2.8 0v1.5h1.5V15zm2.7 0v1.5H14V15z"/></svg>
          0400 555 219
        </span>
      </li>
      <li>
        <svg viewBox="0 0 20 20" aria-hidden="true"><path d="M5 2h8l2 2v4H5zM2 9h16a1 1 0 0 1 1 1v6a1 1 0 0 1-1 1h-2v-3H4v3H2a1 1 0 0 1-1-1v-6a1 1 0 0 1 1-1zm3 6h10v3H5z"/></svg>
        08 9555 0143
      </li>
      <li>
        <svg viewBox="0 0 20 20" aria-hidden="true"><path d="M2 7l8-5 8 5v10H2zm1.6 1.2L10 12.4l6.4-4.2L10 4z"/></svg>
        daniel@pinewoodnetworking.com.au
      </li>
      <li>
        <svg viewBox="0 0 20 20" aria-hidden="true"><path d="M10 1a9 9 0 1 0 0 18 9 9 0 0 0 0-18zm-1 2.2V6H6.4A7.3 7.3 0 0 1 9 3.2zm2 0A7.3 7.3 0 0 1 13.6 6H11zM5.6 7.5H9v2H3.3a7 7 0 0 1 2.3-2zm5.4 0h3.4a7 7 0 0 1 2.3 2H11zM3.3 11H9v2H5.6a7 7 0 0 1-2.3-2zm7.7 0h5.7a7 7 0 0 1-2.3 2H11zM6.4 14.5H9v2.3a7.3 7.3 0 0 1-2.6-2.3zm4.6 0h2.6a7.3 7.3 0 0 1-2.6 2.3z"/></svg>
        www.pinewoodnetworking.com.au
      </li>
    </ul>

    <address class="address">
      Unit 7 22 Carrow Street<br>
      Bellmont WA 6150
    </address>
  </section>

  <section class="card card--back" aria-label="Card back">
    <h1 class="back-brand">
      <span class="back-brand__top">Pinewood</span>
      <span class="back-brand__bottom">Networking</span>
    </h1>
    <p class="tagline">Complete IT Management</p>
    <p class="back-web">www.<strong>pinewoodnetworking</strong>.com.au</p>
  </section>

</div>
</body>
</html>
```